Year 12 Chemistry Workbook illustrations and diagrams

We are producing a Chemistry Workbook for senior high-school students in South Australia and require a designer to create illustrations including detailed diagrams and graphs for our upcoming publication.

The attached files are illustrations that we'd like to have recreated, with your own personal style incorporated.

We will require you to do the following:
- Create vector artwork
- Supply AI files
- Use the font helvetica neue 45 light, or its italic variation
- Use full colour wherever possible
- Please use 100% black, not RGB black/eye-dropped black

Target Market(s)

Senior high school students

Industry/Entity Type

School

Font styles to use
Sans Serif

Colors

Designer to choose colors to be used in the design.

Requirements
Must have
• - Create vector artwork
• - Supply AI files
• - Use the font helvetica neue 45 light, or its italic variation
• - Use full colour wherever possible
• - Please use 100% black, not RGB black/eye-dropped black
Should not have
• Please do not use RGB black/eye-dropped black

```html
<!DOCTYPE html>
<html lang="en">
<head>
<meta charset="utf-8">
<title>Oil accumulation process in an oleaginous microorganism</title>
<link href="https://fonts.googleapis.com/css2?family=Arimo:wght@400;700&display=swap" rel="stylesheet">
<style>
  :root {
    --page: #ffffff;
    --ink: #000000;
    --panel: #80b8ff;
    --plot: #ffffff;
    --nitrogen: #e60000;
    --glucose: #ff4a0a;
    --biomass: #6a2cf0;
    --lipid: #2fd61e;
  }
  html, body {
    margin: 0;
    padding: 0;
    width: 1200px;
    height: 844px;
    overflow: hidden;
    background: var(--page);
  }
  .figure {
    display: block;
    width: 1200px;
    height: 844px;
    font-family: "Arimo", Arial, sans-serif;
  }
  .caption { font-size: 13.5px; fill: var(--ink); }
  .panel { fill: var(--panel); }
  .chart-title { font-size: 16px; font-weight: 700; fill: var(--ink); }
  .plot-area { fill: var(--plot); }
  .axis { stroke: var(--ink); stroke-width: 0.8; fill: none; }
  .tick-label { font-size: 5px; fill: var(--ink); }
  .axis-title { font-size: 8px; fill: var(--ink); }
  .phase-label { font-size: 8.5px; fill: var(--ink); }
  .phase-arrow { stroke: var(--ink); stroke-width: 0.9; fill: none; }
  .arrow-head { fill: var(--ink); }
  .curve { fill: none; stroke-width: 2; stroke-linecap: round; }
  .curve-nitrogen { stroke: var(--nitrogen); }
  .curve-glucose { stroke: var(--glucose); }
  .curve-biomass { stroke: var(--biomass); }
  .curve-lipid { stroke: var(--lipid); }
  .series-label { font-size: 8.5px; }
  .label-nitrogen { fill: var(--nitrogen); }
  .label-glucose { fill: var(--glucose); }
  .label-biomass { fill: var(--biomass); }
  .label-lipid { fill: var(--lipid); }
</style>
</head>
<body>
<svg class="figure" viewBox="0 0 842 592.2" xmlns="http://www.w3.org/2000/svg">
  <text class="caption" x="63" y="52">The following graph represents the relative changes in glucose, lipids (oils), and biomass for algae durnig their growth</text>

  <rect class="panel" x="148" y="88" width="547" height="442"/>

  <text class="chart-title" x="421" y="138" text-anchor="middle">Oil accumulation process in an</text>
  <text class="chart-title" x="421" y="161" text-anchor="middle">oleaginous microorganism</text>

  <g class="phases">
    <line class="phase-arrow" x1="282" y1="219" x2="370" y2="219"/>
    <path class="arrow-head" d="M277,219 l7,-3 v6 z"/>
    <path class="arrow-head" d="M373,219 l-7,-3 v6 z"/>
    <line class="phase-arrow" x1="375" y1="208" x2="375" y2="240"/>
    <line class="phase-arrow" x1="380" y1="219" x2="420" y2="219"/>
    <line class="phase-arrow" x1="514" y1="219" x2="562" y2="219"/>
    <path class="arrow-head" d="M377,219 l7,-3 v6 z"/>
    <path class="arrow-head" d="M567,219 l-7,-3 v6 z"/>
    <text class="phase-label" x="322" y="215" text-anchor="middle">Balanced</text>
    <text class="phase-label" x="322" y="229" text-anchor="middle">growth</text>
    <text class="phase-label" x="467" y="222" text-anchor="middle">Liquid accumulation</text>
  </g>

  <rect class="plot-area" x="277" y="240" width="290" height="215"/>

  <g class="axes">
    <line class="axis" x1="277" y1="240" x2="277" y2="462"/>
    <line class="axis" x1="266" y1="240" x2="277" y2="240"/>
    <line class="axis" x1="266" y1="293" x2="277" y2="293"/>
    <line class="axis" x1="266" y1="346" x2="277" y2="346"/>
    <line class="axis" x1="266" y1="399" x2="277" y2="399"/>
    <line class="axis" x1="266" y1="452" x2="277" y2="452"/>
    <line class="axis" x1="567" y1="240" x2="567" y2="462"/>
    <line class="axis" x1="567" y1="262" x2="578" y2="262"/>
    <line class="axis" x1="567" y1="323" x2="578" y2="323"/>
    <line class="axis" x1="567" y1="388" x2="578" y2="388"/>
    <line class="axis" x1="567" y1="452" x2="578" y2="452"/>
    <line class="axis" x1="348" y1="455" x2="348" y2="465"/>
    <line class="axis" x1="420" y1="455" x2="420" y2="465"/>
    <line class="axis" x1="493" y1="455" x2="493" y2="465"/>
    <line class="axis" x1="565" y1="455" x2="565" y2="465"/>

    <text class="tick-label" x="262" y="236">100</text>
    <text class="tick-label" x="264" y="290">75</text>
    <text class="tick-label" x="264" y="343">50</text>
    <text class="tick-label" x="264" y="396">25</text>
    <text class="tick-label" x="265" y="449">0</text>
    <text class="tick-label" x="568" y="258">90</text>
    <text class="tick-label" x="568" y="320">60</text>
    <text class="tick-label" x="568" y="384">30</text>
    <text class="tick-label" x="568" y="449">0</text>
    <text class="tick-label" x="280" y="462">0</text>
    <text class="tick-label" x="351" y="463">25</text>
    <text class="tick-label" x="423" y="463">50</text>
    <text class="tick-label" x="496" y="463">75</text>
    <text class="tick-label" x="568" y="463">100</text>

    <text class="axis-title" x="420" y="482" text-anchor="middle">Time (arbitary scale)</text>
    <text class="axis-title" transform="translate(238 345) rotate(-90)" text-anchor="middle">Glucose/Nitrogen</text>
    <text class="axis-title" transform="translate(249 345) rotate(-90)" text-anchor="middle">(arbitary values)</text>
    <text class="axis-title" transform="translate(604 345) rotate(90)" text-anchor="middle">Biomass (dry wt)</text>
    <text class="axis-title" transform="translate(593 345) rotate(90)" text-anchor="middle">Lipid (% dry wt)</text>
  </g>

  <g class="curves">
    <path class="curve curve-glucose" d="M277,240 C330,246 380,296 430,356 S530,428 567,441"/>
    <path class="curve curve-biomass" d="M277,441 C300,442 325,410 350,378 S405,295 430,285 S520,253 567,253"/>
    <path class="curve curve-lipid" d="M277,425 L370,426 C420,426 445,410 470,375 C500,345 515,285 567,278"/>
    <path class="curve curve-nitrogen" d="M277,240 C300,238 318,248 332,290 S360,420 368,455"/>
  </g>

  <text class="series-label label-biomass" x="427" y="270">Biomass</text>
  <text class="series-label label-nitrogen" x="300" y="334">Nitrogen</text>
  <text class="series-label label-lipid" x="480" y="322">Lipid</text>
  <text class="series-label label-glucose" x="505" y="437">Glucose</text>
</svg>
</body>
</html>
```